Stationary design for boutique production house

We need a stationary design for our production house, 'Lorno Productions' based in Singapore. We produce microfilms as well as podcasts, talkshows and events. Our logo is a stylized icon of our director, who is also the executive producer and host of our programs, Lorno. Our main company colors are Red, Black and white. We would like a clean, minimalist design incorporating our existing company logo that conveys a sense of urbanism and elegance.

Logo and font files are attached. f

Target Market(s)

We focus on lifestyle media rather than entertainment.

Industry/Entity Type

Boutique

Font styles to use
Serif
Sans Serif

Colors
ec1f27
ffffff
000000

Requirements
Must have
• Our company logo and at least one of our company colors.
Nice to have
• Our address and contact information.
Should not have
• Changes made to the company logo (using only certain parts of it is fine though)

```html
<!DOCTYPE html>
<html lang="en">
<head>
<meta charset="utf-8">
<title>Lorno Productions — Stationery</title>
<link rel="stylesheet" href="https://fonts.googleapis.com/css2?family=Open+Sans:wght@400;600;700&family=Montserrat:wght@500&display=swap">
<style>
:root{
  --red:#ec1f27;
  --ink:#333333;
  --black:#000000;
  --paper:#ffffff;
  --backdrop:#ececec;
  --text:#555555;
  --sans:'Open Sans', Arial, sans-serif;
}
*{margin:0;padding:0;box-sizing:border-box}
html,body{width:1200px;height:937px;overflow:hidden;background:var(--backdrop)}
.canvas{position:relative;width:1200px;height:937px}
.sheet{position:absolute;background:var(--paper);overflow:hidden}
.sheet > svg.swoosh{position:absolute;inset:0;width:100%;height:100%}

/* brand lockup: plain circle + name in one colour and weight */
.brand{position:absolute;display:flex;flex-direction:column;align-items:center}
.brand-mark{border-radius:50%;background:var(--ink);flex:none}
.brand-name{font-family:var(--sans);font-weight:700;color:var(--ink);text-transform:uppercase;text-align:center;line-height:1.25;letter-spacing:.1em;white-space:nowrap}

/* letterhead */
.letterhead{left:185px;top:67px;width:385px;height:545px}
.letterhead .brand{left:14px;top:24px;width:124px}
.letterhead .brand-mark{width:100px;height:100px}
.letterhead .brand-name{font-size:11px;margin-top:12px}
.letter{position:absolute;left:36px;top:204px;width:254px;font-family:var(--sans);font-size:4.4px;line-height:7px;color:var(--text)}
.letter p{margin-bottom:8px}
.letter .date{margin-bottom:5px}
.letter .recipient{margin-bottom:5px}
.letter .gap{margin-bottom:22px}
.letter strong{color:var(--ink);font-weight:700}
.signature{width:22px;height:14px;background:linear-gradient(90deg,#777,#bbb);margin:4px 0 6px;border-radius:2px}
.letter-footer{position:absolute;left:12px;top:474px;font-family:var(--sans);font-size:3.8px;line-height:6px;color:var(--text)}
.letter-footer strong{color:var(--ink)}

/* presentation sheet */
.cover{left:636px;top:40px;width:458px;height:576px}
.cover .brand{left:0;right:0;top:160px}
.cover .brand-mark{width:160px;height:160px}
.cover .brand-name{font-size:20px;margin-top:26px}

/* business cards */
.card{border-radius:8px}
.card-front{left:45px;top:658px;width:177px;height:100px}
.card-front .brand{left:14px;top:8px;width:62px}
.card-front .brand-mark{width:38px;height:38px}
.card-front .brand-name{font-size:4.6px;margin-top:4px}
.card-holder{position:absolute;right:8px;top:9px;text-align:right;font-family:var(--sans);color:var(--ink)}
.card-holder .name{font-size:5.6px;font-weight:600;letter-spacing:.04em}
.card-holder .role{font-size:3.8px;font-weight:700}
.card-contact{position:absolute;right:8px;top:50px;text-align:right;font-family:var(--sans);font-size:3.2px;line-height:5px;color:var(--ink)}
.card-back{left:45px;top:785px;width:177px;height:99px}
.card-back .brand{left:0;right:0;top:20px}
.card-back .brand-mark{width:38px;height:38px}
.card-back .brand-name{font-size:4.8px;margin-top:5px}

/* envelopes */
.envelope-front{left:264px;top:671px;width:433px;height:209px}
.envelope-front .brand{left:10px;top:20px;width:86px}
.envelope-front .brand-mark{width:64px;height:64px}
.envelope-front .brand-name{font-size:7px;margin-top:8px}
.envelope-back{left:736px;top:671px;width:432px;height:209px}
.envelope-flap{position:absolute;left:0;top:0;width:100%;height:72px;background:var(--ink);border-radius:0 0 40px 40px}
.envelope-url{position:absolute;left:0;right:0;top:30px;text-align:center;font-family:'Montserrat',Arial,sans-serif;font-weight:500;font-size:12.5px;letter-spacing:.16em;color:var(--paper)}
</style>
</head>
<body>
<main class="canvas">

  <section class="sheet letterhead">
    <svg class="swoosh" viewBox="0 0 385 545" preserveAspectRatio="none" aria-hidden="true">
      <path d="M228 0 Q350 30 385 170 L385 0 Z" fill="var(--ink)"/>
      <path d="M330 0 Q372 22 385 72 L385 0 Z" fill="var(--paper)"/>
      <path d="M338 0 Q376 20 385 60 L385 0 Z" fill="var(--red)"/>
      <path d="M228 0 Q372 40 385 300" fill="none" stroke="#e4e4e4" stroke-width="1"/>
    </svg>
    <div class="brand">
      <div class="brand-mark"></div>
      <div class="brand-name">Lorno<br>Productions</div>
    </div>
    <div class="letter">
      <p class="date">July 2, 2024</p>
      <p class="recipient"><strong>Dear Sir,</strong><br>18 Keong Saik Road, Singapore</p>
      <p>Thank you for your interest in our studio. We create short films, podcasts, talk shows and live events with a focus on lifestyle stories. Our small team handles every stage, from early concept and scripting through filming, editing and final delivery. We would be glad to share a proposal and a schedule that suits your plans and budget for the coming season.</p>
      <p class="gap">Our studio in Singapore is open for visits by appointment. Please let us know a date that works for you and your team.</p>
      <p>We look forward to working together on a project that reflects your brand with care and clarity. Every production is planned closely with our clients so that the final piece feels natural, polished and true to its audience. Should you need any further details about our rates, our recent work or our crew, please contact our office at any time.</p>
      <p>Best Regards,</p>
      <div class="signature" role="img" aria-label="Handwritten signature"></div>
      <p><strong>Daniel Reyes</strong><br>Director<br>18 Keong Saik Road, Singapore</p>
    </div>
    <div class="letter-footer">
      <strong>18 Keong Saik Road</strong><br><strong>Singapore 089133</strong><br><br>
      +65 6123 4567<br>+65 6123 4568<br>+65 6123 4569<br>hello@lornostudio.sg<br>www.lornostudio.sg
    </div>
  </section>

  <section class="sheet cover">
    <svg class="swoosh" viewBox="0 0 458 576" preserveAspectRatio="none" aria-hidden="true">
      <path d="M208 0 Q420 40 458 220 L458 0 Z" fill="var(--ink)"/>
      <path d="M370 0 Q440 30 458 110 L458 0 Z" fill="var(--paper)"/>
      <path d="M380 0 Q446 28 458 95 L458 0 Z" fill="var(--red)"/>
    </svg>
    <div class="brand">
      <div class="brand-mark"></div>
      <div class="brand-name">Lorno Productions</div>
    </div>
  </section>

  <section class="sheet card card-front">
    <svg class="swoosh" viewBox="0 0 177 100" preserveAspectRatio="none" aria-hidden="true">
      <path d="M0 22 Q4 92 110 100 L0 100 Z" fill="var(--red)"/>
      <path d="M0 34 Q8 92 96 100 L0 100 Z" fill="var(--paper)"/>
      <path d="M0 40 Q10 94 88 100 L0 100 Z" fill="var(--ink)"/>
    </svg>
    <div class="brand">
      <div class="brand-mark"></div>
      <div class="brand-name">Lorno<br>Productions</div>
    </div>
    <div class="card-holder">
      <div class="name">AVERY TAN</div>
      <div class="role">PRESIDENT</div>
    </div>
    <div class="card-contact">
      <strong>18 Keong Saik Road</strong><br><strong>Singapore 089133</strong><br><br>
      +65 6123 4567<br>+65 6123 4568<br>+65 6123 4569<br>hello@lornostudio.sg<br>www.lornostudio.sg
    </div>
  </section>

  <section class="sheet card card-back">
    <div class="brand">
      <div class="brand-mark"></div>
      <div class="brand-name">Lorno<br>Productions</div>
    </div>
  </section>

  <section class="sheet envelope-front">
    <svg class="swoosh" viewBox="0 0 433 209" preserveAspectRatio="none" aria-hidden="true">
      <path d="M246 209 Q380 150 366 0 L433 0 L433 209 Z" fill="var(--red)"/>
      <path d="M296 209 Q396 140 374 0 L433 0 L433 209 Z" fill="var(--paper)"/>
      <path d="M304 209 Q402 140 380 0 L433 0 L433 209 Z" fill="var(--ink)"/>
    </svg>
    <div class="brand">
      <div class="brand-mark"></div>
      <div class="brand-name">Lorno<br>Productions</div>
    </div>
  </section>

  <section class="sheet envelope-back">
    <div class="envelope-flap"></div>
    <div class="envelope-url">www.lornostudio.sg</div>
  </section>

</main>
</body>
</html>
```